Catering Menu Package

I currently have a complete menu package, which we have redesigned as far as content, now I need to it put together in a catalog type format. It is essentially 10-12 pages in length, and will be sent for print production. Upon receiving a final edit
Updates

I have added an example gif to the project.

I did this free hand this basically what I am looking for. please change text and type to whatever you think would look best. This is a total rough design so, feel free to change any and everything. The text for the page is on the word documents. If you need more images let me know I am in the process of getting as many images uploaded for your use.

Project Deadline Extended
Reason: I figured we got a late jump with questions, so i am extending a few days .

Target Market(s)

The target market is business who wish to have catered luncheons, breakfasts , meetings

Industry/Entity Type

Catering

Requirements
Must have
• I have attached a copy of the text that what we want in the package, our logo, and i have also attached a catering package of another company to give you an idea what the finished product will be
Should not have
• It should not look identical to the example catering packages, these are for some inspiration we want our own design with the same type of look and feel

```html
<!DOCTYPE html>
<html lang="en">
<head>
<meta charset="utf-8">
<title>Harvest Table Caterers – More Signature Soups &amp; Beverages</title>
<link href="https://fonts.googleapis.com/css2?family=Pinyon+Script&family=Libre+Baskerville:ital,wght@0,400;1,700&display=swap" rel="stylesheet">
<style>
  :root {
    --ink: #2b2622;
    --body-ink: #3d3631;
    --accent: #9a6a2f;
    --script-ink: #5a4d44;
    --page: #ffffff;
    --margin-tan: #d9c7b8;
    --margin-light: #f4eee9;
    --brand: #2b2622;
  }
  * { margin: 0; padding: 0; box-sizing: border-box; }
  html, body { width: 1200px; height: 927px; overflow: hidden; }
  body {
    position: relative;
    font-family: "Libre Baskerville", Georgia, serif;
    color: var(--body-ink);
    background: var(--page);
  }
  .margin-band {
    position: absolute; left: 0; top: 0; width: 184px; height: 927px;
    background: linear-gradient(180deg, var(--page) 0%, var(--margin-light) 45%, var(--margin-tan) 100%);
  }
  .content-panel {
    position: absolute; left: 184px; top: 0; width: 1016px; height: 927px;
    background: linear-gradient(160deg, #ffffff 0%, #faf8f6 60%, #f2ece8 100%);
  }
  .brand {
    position: absolute; left: 28px; top: 40px; width: 140px;
    display: flex; flex-direction: column; align-items: center; gap: 14px;
  }
  .brand-mark { width: 40px; height: 40px; background: var(--brand); }
  .brand-name {
    font-family: "Libre Baskerville", Georgia, serif;
    font-size: 19px; line-height: 26px; text-align: center;
    color: var(--brand); font-weight: 400;
  }
  .section-title {
    position: absolute;
    font-family: "Pinyon Script", cursive;
    font-weight: 400; color: var(--script-ink);
    text-shadow: 1px 2px 2px rgba(0,0,0,0.18);
  }
  .soups-title { left: 203px; top: 52px; font-size: 44px; }
  .beverages-title { left: 688px; top: 104px; font-size: 44px; }
  .soup-list { position: absolute; left: 197px; top: 128px; width: 440px; list-style: none; }
  .soup { margin-bottom: 24px; }
  .soup-name {
    font-style: italic; font-weight: 700; color: var(--accent);
    font-size: 17px; line-height: 24px;
  }
  .soup-desc { font-size: 16px; line-height: 24px; color: var(--body-ink); }
  .beverage-list { position: absolute; left: 689px; top: 176px; list-style: none; }
  .beverage { font-size: 16px; line-height: 36.5px; color: var(--ink); }
  .beverage.accent { color: var(--accent); }
  .photo { position: absolute; }
  .photo-soup {
    left: 212px; top: 539px; width: 603px; height: 362px;
    background: linear-gradient(135deg, #b99470 0%, #d6b48c 40%, #e9763a 60%, #f3efe9 100%);
  }
  .photo-tea {
    left: 832px; top: 380px; width: 301px; height: 449px;
    background: linear-gradient(180deg, #3cb8c4 0%, #e8c26a 30%, #d58a2a 65%, #a14a14 100%);
  }
</style>
</head>
<body>
  <div class="margin-band"></div>
  <div class="content-panel"></div>

  <div class="brand">
    <span class="brand-mark"></span>
    <span class="brand-name">Harvest<br>Table<br>Caterers</span>
  </div>

  <h1 class="section-title soups-title">More Signature Soups</h1>
  <ul class="soup-list">
    <li class="soup">
      <p class="soup-name">Fire-Roasted Tomato Bisque</p>
      <p class="soup-desc">Creamy tomato soup.&nbsp; Finished with<br>Parmesan-Garlic Croutons.Vegetarian.</p>
    </li>
    <li class="soup">
      <p class="soup-name">Navy Bean &amp; Country Ham</p>
      <p class="soup-desc">Made with just like Grandma used to with<br>the Smoked Ham hocks.</p>
    </li>
    <li class="soup">
      <p class="soup-name">Creamy Broccoli &amp; Cheddar Soup</p>
    </li>
    <li class="soup">
      <p class="soup-name">Beef Vegetable</p>
      <p class="soup-desc">Chef Marlow’s secret recipe!&nbsp; Slow cooked with<br>generous amounts of Beef &amp; seasonal Vegetables.</p>
    </li>
  </ul>

  <h2 class="section-title beverages-title">Beverages</h2>
  <ul class="beverage-list">
    <li class="beverage">Assorted Sodas</li>
    <li class="beverage accent">Water &amp; Ice</li>
    <li class="beverage">Southern Style Sweet Tea</li>
    <li class="beverage accent">Lemonade</li>
    <li class="beverage">Bottled Water</li>
  </ul>

  <div class="photo photo-soup" role="img" aria-label="Photo of a white bowl of tomato bisque with a spoon and crackers on a woven placemat"></div>
  <div class="photo photo-tea" role="img" aria-label="Photo of glasses of iced sweet tea with lemon slices and mint"></div>
</body>
</html>
```